Etiketten für Honig
Wir können nur volle Punktzahl geben. Roswitha ist selbst Ideenreich, wirklich nett und setzte unsere Ideen schnell und engagiert um. Hat echt Spass gemacht mit ihr zu arbeiten.
Zielgruppe
Es scheint Missverständnisse zu geben weshalb ich das Briefing wohl ändern muss.
see below for English translation
Wir sind eine kleine Imkerei, die von der Liebhaberei in den Nebenerwerb wechselt. Wir verkaufen verschiedene Sortenhonige und Honigzubereitungen (siehe Webseite) im vorwiegend ländlichen Raum des Münsterlandes.
Entsprechend unseres Standortes und unserer Kundschaft benötigen wir ein klassisch ländliches Design. Hierfür haben wir auch bereits ein Logo welches verwendet werden muss.
English
There seems to be some misunderstanding, so I guess I'll have to change the briefing.
We are a small apiary that changes from hobby to sideline. We sell different types of honey and honey preparations (e.g. honey with raspberry) in a predominantly rural area of the Münsterland (Muensterland).
According to our location and our clientele, we need a classic rural design. We already have a logo which must be used.
Aufgabenstellung
Wir möchten ein rechteckiges Etikett mit Gewährverschluss das für verschiedene Sorten adoptierbar ist. Zum Beispiel durch den Austausch der Sortenbezeichnung und eine farbliche Veränderung.
Das Design soll später auf Naturpapier oder Graspapier gedruckt werden. Das Logo muss auf Etikett und Gewährverschluss abgebildet werden.
We would like a rectangular label with a guarantee seal that is adoptable for different varieties. For example, by exchanging the variety designation and changing the color.
The design will later be printed on uncoated paper or grass paper. The logo must be shown on the label and guarantee seal.

```html
<!DOCTYPE html>
<html lang="de">
<head>
<meta charset="utf-8">
<title>Etiketten – Eichtaler Landhonig</title>
<link href="https://fonts.googleapis.com/css2?family=Montserrat:wght@300;400;500&family=Allura&display=swap" rel="stylesheet">
<style>
  :root{
    --paper:#ffffff;
    --ink:#5a5a5a;
    --ink-dark:#3f3f3f;
    --rule:#9a9a9a;
    --brand-green:#8cb33a;
    --brand-gold:#e9b21c;
    --flower-pink:#f2a7b8;
    --flower-violet:#8a6bb5;
    --flower-orange:#f28a2e;
    --leaf:#6f9a5b;
    --leaf-dark:#3f6b45;
  }
  *{box-sizing:border-box;margin:0;padding:0}
  html,body{width:1200px;height:1054px;overflow:hidden;background:var(--paper)}
  body{position:relative;font-family:"Montserrat",sans-serif;color:var(--ink)}

  .seal{position:absolute;width:158px;height:158px;border:1px solid var(--rule);border-radius:50%;background:var(--paper);z-index:2;text-align:center}
  .seal-strip{position:absolute;width:97px;height:90px;border-left:1px solid var(--rule);border-right:1px solid var(--rule)}
  .seal .brand{margin-top:16px}
  .seal .variety{font-size:17px;font-weight:400;letter-spacing:-.2px;margin-top:6px;color:var(--ink)}
  .seal .flowers{width:70px;height:46px;margin:6px auto 0;border-radius:40%;
    background:radial-gradient(circle at 60% 55%,#f6c94a 0 18%,transparent 40%),
               radial-gradient(circle at 25% 35%,var(--flower-orange) 0 14%,transparent 35%),
               radial-gradient(ellipse at 50% 50%,#a9c99a 0,transparent 70%)}

  .brand{display:flex;flex-direction:column;align-items:center;gap:3px}
  .brand .dot{width:20px;height:20px;border:2px solid var(--brand-green);border-radius:50%}
  .brand .name{font-size:14px;font-weight:400;color:var(--ink-dark);letter-spacing:.3px}

  .label{position:absolute;width:376px;height:215px;border:1px solid var(--rule);background:var(--paper);overflow:hidden}
  .label .brand{position:absolute;left:0;right:0}
  .label .script{position:absolute;left:0;right:0;text-align:center;font-family:"Allura",cursive;font-size:34px;color:var(--ink-dark);white-space:nowrap}
  .label .variety{position:absolute;left:0;right:0;text-align:center;font-size:22px;font-weight:400;color:var(--ink)}
  .label .weight{position:absolute;font-size:16px;font-style:italic;font-weight:300;color:var(--ink-dark)}

  .floral-top{position:absolute;left:0;top:0;width:175px;height:140px;
    background:radial-gradient(circle at 22% 20%,var(--flower-pink) 0 14%,transparent 30%),
               radial-gradient(circle at 15% 55%,var(--flower-violet) 0 10%,transparent 26%),
               radial-gradient(circle at 55% 14%,#f6c94a 0 8%,transparent 20%),
               radial-gradient(ellipse at 30% 30%,#b8d3a7 0,transparent 70%)}
  .floral-bottom{position:absolute;right:0;bottom:0;width:180px;height:140px;
    background:radial-gradient(circle at 85% 80%,var(--flower-pink) 0 14%,transparent 30%),
               radial-gradient(circle at 80% 45%,var(--flower-violet) 0 10%,transparent 24%),
               radial-gradient(circle at 40% 85%,var(--flower-orange) 0 7%,transparent 18%),
               radial-gradient(ellipse at 70% 70%,#b8d3a7 0,transparent 70%)}
  .foliage{position:absolute;left:0;right:0;bottom:0;height:95px;
    background:linear-gradient(180deg,rgba(255,255,255,0) 0,#c9dcb8 35%,var(--leaf) 75%,#8fb07a 100%)}
  .weight-badge{position:absolute;left:12px;bottom:-14px;width:52px;height:52px;border:1px solid var(--rule);border-radius:50%;background:var(--paper)}

  .back{position:absolute;left:166px;top:580px;width:319px;height:215px;border:1px solid var(--rule);background:var(--paper);overflow:hidden}
  .back h2{position:absolute;left:10px;top:24px;font-size:16.4px;font-weight:400;letter-spacing:-.25px;color:var(--ink);white-space:nowrap}
  .back .notes{position:absolute;left:9px;top:52px;font-size:11.4px;line-height:15.5px;letter-spacing:-.2px;color:var(--ink);white-space:nowrap}
  .back .brand{position:absolute;left:42px;top:92px}
  .back .brand .name{font-size:12px}
  .back address{position:absolute;left:11px;top:143px;font-style:normal;font-size:9.4px;line-height:11.3px;letter-spacing:-.15px;color:var(--ink-dark);white-space:nowrap}
  .back .bbd{position:absolute;left:199px;top:137px;font-size:9.4px;letter-spacing:-.15px;color:var(--ink-dark);white-space:nowrap}
</style>
</head>
<body>

  <!-- Frühtracht set -->
  <div class="seal-strip" style="left:277px;top:209px"></div>
  <div class="seal" style="left:247px;top:68px">
    <div class="brand"><span class="dot"></span><span class="name">Kellbrunn</span></div>
    <div class="variety">FRÜHTRACHT</div>
    <div class="flowers" role="img" aria-label="Aquarell-Blumenzweig in Orange und Gelb"></div>
  </div>
  <div class="label" style="left:135px;top:296px">
    <div class="floral-top" role="img" aria-label="Aquarell-Blumenranke mit Rosen und Wildblumen"></div>
    <div class="floral-bottom" role="img" aria-label="Aquarell-Blumenranke mit Rosen und Wildblumen"></div>
    <div class="brand" style="top:12px;left:120px;right:0"><span class="dot"></span><span class="name">Kellbrunn</span></div>
    <div class="script" style="top:80px">Eichtaler Landhonig</div>
    <div class="variety" style="top:127px;left:-10px">FRÜHTRACHT</div>
    <div class="weight" style="left:9px;top:190px">250g</div>
  </div>

  <!-- Waldhonig set -->
  <div class="seal-strip" style="left:784px;top:213px"></div>
  <div class="seal" style="left:754px;top:72px">
    <div class="brand"><span class="dot"></span><span class="name">Kellbrunn</span></div>
    <div class="variety">FRÜHTRACHT</div>
    <div class="flowers" role="img" aria-label="Aquarell-Blumenzweig in Orange und Gelb"></div>
  </div>
  <div class="label" style="left:642px;top:297px">
    <div class="foliage" role="img" aria-label="Aquarell-Blätterborte in Grüntönen"></div>
    <div class="weight-badge"></div>
    <div class="brand" style="top:8px"><span class="dot"></span><span class="name">Kellbrunn</span></div>
    <div class="script" style="top:70px">Eichtaler Landhonig</div>
    <div class="variety" style="top:116px">WALDHONIG</div>
    <div class="weight" style="left:18px;top:190px">250g</div>
  </div>

  <!-- Rückseite -->
  <div class="back">
    <h2>Echter Honig aus dem Münsterland</h2>
    <p class="notes">Mehrwegglas, Honig aus Deutschland.<br>Trocken, dunkel und vor Wärme geschützt lagern.</p>
    <div class="brand"><span class="dot"></span><span class="name">Kellbrunn</span></div>
    <address>Honigmanufaktur Kellbrunn<br>Heideweg 12<br>48999 Lindenfeld<br>Tel. 01234 567890<br>www.honigmanufaktur-kellbrunn.de</address>
    <p class="bbd">Mindestens haltbar bis:</p>
  </div>

</body>
</html>
```